Book Cover on Entrepreneurship for Eye Doctors

Book Title: The Lens Practice Builder: How to launch with confidence
Author: Rufus Tembley, Optom, MBA, DBA, EIC
I need a Book Cover with the following descriptions:
Topic: the book topic is entrepreneurship knowledge for eye care professionals.
The book's audience: eye care professionals who you know as Opticians, who sell eyeglasses and sunglasses;
Optometrists, test eyes, fit contact lenses, and prescribe medication
Ophthalmologists, perform eye surgery
More about the audience:
1- Young eye care professionals who don’t know about entrepreneurship and those who are stuck in the 9-to-5 job;
2- This is the first book written on entrepreneurship with eye care professionals in mind.
3- Private practice owners the established business guys who are looking to grow their business;
4- Many eye care professionals are MBA holders they may have learned a little bit about entrepreneurship during their MBA studies.
Use the sample cover above and the suggestions that follow as a guide:
1- The cover should be very simple leaving an empty space somewhere to sign the book;
2- The Title and author name should use a modern font;
3- The cover should provide info about what's inside the book through illustrations, for example:
a- Gears: illustrating entrepreneur growth mindset (or anything more explicit)
b- Spectacles, sunglasses, lenses, eye drops, or any other eye care-related correction tools illustrating eye care (or anything more explicit)
c- Symbols illustrating ideas, opportunity, and profit, like money, charts, light bulbs, brain, and coins,...(or anything more explicit)
d- Entrepreneurship illustrated by Briefcase, tie, suit,... (or anything more explicit)

The rest is your creativity and imagination interplay.

Target Market(s)

Eye care professionals: Opticians, Optometrists, Ophthalmologists, Eye Care Administrators, Students in eye specialties.

Industry/Entity Type

eye care

Requirements
Must have
• 1- The cover should be very simple leaving an empty space somewhere to sign the book; 2- The Title and author name should use a modern font; 3- The cover should provide info about what's inside the book through illustrations, for example: a- Gears: illustrating entrepreneur growth mindset (or anything more explicit) b- Spectacles, sunglasses, lenses, eye drops, or any other eye care-related correction tools illustrating eye care (or anything more explicit) c- Symbols illustrating ideas, opportunity, and profit, like money, charts, light bulbs, brain, and coins,...(or anything more explicit) d- Entrepreneurship illustrated by Briefcase, tie, suit,... (or anything more explicit)

```html
<!DOCTYPE html>
<html lang="en">
<head>
<meta charset="utf-8">
<title>The Lens Practice Builder — Cover Wrap</title>
<link href="https://fonts.googleapis.com/css2?family=Bebas+Neue&family=Montserrat:wght@400;600&display=swap" rel="stylesheet">
<style>
  :root {
    --navy: #1b3350;
    --navy-deep: #14283f;
    --teal: #22acd0;
    --paper: #e9f4f5;
    --paper-soft: #f3f9f9;
    --ink: #233247;
    --stage: #e4e6e8;
  }
  * { box-sizing: border-box; margin: 0; padding: 0; }
  html, body { width: 1200px; height: 924px; overflow: hidden; background: var(--stage); }
  .wrap {
    position: absolute; left: 20px; top: 22px;
    width: 1160px; height: 880px;
    display: flex;
    box-shadow: 0 6px 24px rgba(0,0,0,.15);
  }
  .panel { position: relative; height: 880px; background: var(--paper); overflow: hidden; }
  .back { width: 560px; }
  .spine { width: 40px; background: linear-gradient(90deg, #dfeeef, var(--paper-soft), #dfeeef); }
  .front { width: 560px; }

  .band {
    position: absolute; left: 0; right: 0; bottom: 0; height: 80px;
    background: var(--navy-deep);
  }

  /* Back cover */
  .back-title {
    position: absolute; top: 34px; left: 0; right: 0;
    text-align: center;
    font-family: "Bebas Neue", sans-serif;
    color: var(--navy); line-height: .86;
  }
  .back-title .l1, .back-title .l2 { font-size: 62px; display: block; }
  .back-title .l3 { font-size: 40px; color: var(--teal); display: block; margin-top: 4px; }
  .blurb {
    position: absolute; top: 212px; left: 30px; right: 30px;
    font-family: "Montserrat", sans-serif; font-size: 9.6px; line-height: 1.42;
    color: var(--ink); text-align: justify;
  }
  .blurb p + p { margin-top: 8px; }
  .back-author {
    position: absolute; top: 578px; left: 0; right: 0; text-align: center;
    font-family: "Bebas Neue", sans-serif; font-size: 22px; letter-spacing: 2.5px;
    color: var(--navy);
  }
  .author-photo {
    position: absolute; top: 614px; left: 30px; width: 120px; height: 170px;
    background: linear-gradient(180deg, #c9cdd2 0%, #9aa1ab 55%, #2f3846 100%);
  }
  .bio {
    position: absolute; top: 612px; left: 162px; right: 30px;
    font-family: "Montserrat", sans-serif; font-size: 9.2px; line-height: 1.36;
    color: var(--ink); text-align: justify;
  }
  .bio strong { font-weight: 600; color: var(--navy-deep); }

  /* Spine */
  .spine-text {
    position: absolute; left: 50%; top: 36px;
    transform: translateX(-50%) rotate(180deg);
    writing-mode: vertical-rl;
    height: 740px;
    display: flex; align-items: center; justify-content: flex-end; gap: 14px;
    white-space: nowrap;
  }
  .spine-title { font-family: "Bebas Neue", sans-serif; font-size: 24px; letter-spacing: 1px; color: var(--navy); }
  .spine-title em { font-style: normal; color: var(--teal); }
  .spine-author { font-family: "Montserrat", sans-serif; font-weight: 600; font-size: 10px; letter-spacing: 2.5px; color: var(--navy); }

  /* Front cover */
  .hero-art {
    position: absolute; top: 0; left: 0; right: 0; height: 390px;
    background:
      radial-gradient(ellipse at 70% 55%, rgba(90,220,235,.55), transparent 55%),
      radial-gradient(ellipse at 30% 70%, rgba(240,160,120,.35), transparent 50%),
      linear-gradient(180deg, #1f4a6e 0%, #2f6d96 50%, #8fc3d6 82%, var(--paper) 100%);
  }
  .front-title {
    position: absolute; top: 384px; left: 32px; right: 32px;
    font-family: "Bebas Neue", sans-serif; line-height: .9;
    color: var(--navy);
  }
  .front-title span { display: block; }
  .front-title .t1 { font-size: 142px; }
  .front-title .t2 { font-size: 142px; }
  .front-title .t3 { font-size: 118px; color: var(--teal); margin-top: 2px; }
  .subtitle {
    position: absolute; top: 742px; left: 92px; right: 92px;
    text-align: center;
    font-family: "Bebas Neue", sans-serif; font-size: 24px; letter-spacing: 1.5px;
    color: var(--navy);
    border-top: 1.5px solid var(--teal);
    border-bottom: 1.5px solid var(--teal);
    padding: 5px 0 3px;
  }
  .front-author {
    position: absolute; left: 0; right: 0; bottom: 0; height: 80px;
    display: flex; align-items: center; justify-content: center;
    font-family: "Bebas Neue", sans-serif; font-size: 36px; letter-spacing: 1px;
    color: #ffffff;
  }
</style>
</head>
<body>
<div class="wrap">

  <section class="panel back">
    <h2 class="back-title">
      <span class="l1">THE LENS</span>
      <span class="l2">PRACTICE</span>
      <span class="l3">BUILDER</span>
    </h2>
    <div class="blurb">
      <p>Before you decide to enroll in a Master of Business Administration (MBA) program read this book.</p>
      <p>Ophthalmologists, Optometrists, and every eye care professional are lifelong learners. At a certain point during their career they find themselves in need of more business knowledge. Most of them resume their development through completing a Master of Business Administration (MBA) degree or another business degree. I argue that learning entrepreneurship is better than pursuing an MBA. Now I wrote this timely book to provide the basic knowledge that every eye care professional needs to know about entrepreneurship.</p>
      <p>This book does not prepare eye care professionals to work in or on the administrative process, or bring a professional opinion in their department within the practice. Moreover, it does not prepare them to go out of the clinical part of the practice or make a transition to management the way an MBA does. Instead, this book helps them see the “Opportunity” that they are after. It helps them focus on what is best no matter how ambiguous the environment is or the situation they are facing. I argue that an MBA may be useful, however in a rapidly changing world and in the face of uncertainty, an MBA takes long enough time to miss the opportunity they are after as professional learners. In this rapidly changing world I emphasize the importance of developing their entrepreneurial spirit which is somehow different than studying an MBA. All the jobs an MBA will enable the eye care professional to do can be performed by a practice manager or simply outsourced. However, no one can outsource identifying and discovering an entrepreneurial opportunity.</p>
      <p>In this book you navigate through the mind of the entrepreneur and highlight the importance of the entrepreneurial spirit for eye care professionals. You will also understand what makes great eye care entrepreneurs in terms of risk-taking, innovation, and tolerance of ambiguity and answer what an entrepreneurial opportunity is, how to identify it, and what resources are needed in order to identify and capture its value.</p>
    </div>
    <div class="back-author">RUFUS TEMBLEY, OPTOM, MBA, DBA, EIC</div>
    <div class="author-photo" role="img" aria-label="Author portrait photograph"></div>
    <p class="bio"><strong>Doctor Rufus Tembley</strong> is a serial entrepreneur who is specialized in developing and commercializing eye care products and services using business concepts to solve a variety of eye care practices business problems. To this end, he has extensively worked on crowdsourcing, crowdfunding, disruptive innovation, and cult marketing. He built and helped manage Ophthalmology and Optometry practices as well as many optical shops. He is an Optometrist by trade and studied a Doctorate Degree in Business Administration. He has a long history of more than two decades of working in the retail industry. Besides his strong entrepreneurial knowledge, he has an MBA degree in healthcare management from Harbrook University in Larkmoor Valley and a Doctorate degree in Business Administration from Westmere Southern University in Westmere. He is the Editor in Chief at Clear Sight Journal and Digest magazine where he creates and publishes relevant content for helping eye care professionals become better entrepreneurs.</p>
    <div class="band"></div>
  </section>

  <section class="panel spine">
    <div class="spine-text">
      <span class="spine-title">THE LENS PRACTICE <em>BUILDER</em></span>
      <span class="spine-author">RUFUS TEMBLEY, OPTOM, MBA, DBA, EIC</span>
    </div>
    <div class="band"></div>
  </section>

  <section class="panel front">
    <div class="hero-art" role="img" aria-label="Photo of hands working with a glowing business dashboard of charts, gears, eyeglasses and an eye icon"></div>
    <h1 class="front-title">
      <span class="t1">THE LENS</span>
      <span class="t2">PRACTICE</span>
      <span class="t3">BUILDER</span>
    </h1>
    <p class="subtitle">HOW TO LAUNCH WITH CONFIDENCE</p>
    <div class="band"></div>
    <div class="front-author">RUFUS TEMBLEY, OPTOM, MBA, DBA, EIC</div>
  </section>

</div>
</body>
</html>
```